Website design for a high-end equestrian business

Design a website to replace current one. Clean, simple, elegant design. I run a business training show jumping riders and horses, as well as buying and selling high quality horses. I run my business from a beautiful yard in Co. Kildare, Ireland. Reference to Ireland and quality sport horses is important in the website.

Current website is www.orlathornbury.com. One page in particular that I need is a "Sport Horses" page as well as a "References" page. Layout for each to be similar to this one - https://www.brackenleaze.net/en/sporthorses

Another website I like the feel of is www.topcanterstable.com
Colour theme to be charcoal grey with elements of lighter grey and cream, as per logo. Charcoal grey to be somewhat transparent, otherwise it takes over too much. Cream colour is also to be subtle and not too beige.

Please note that Thornbury is one word.

Please note there are new photographs with which to work if desired.

Sick

Target Market(s)

Upmarket clients seeking high quality coaching services and high quality show jumping horses

Number of Pages Required

2 page

Font styles to use
Serif
Sans Serif

Colors

Designer to choose only greyscale colors for use in the design.

Requirements
Must have
• A clean, simple, elegant look to the final design. OVerall theme colours must be subtle and include charcoal grey, light grey and cream. A design that will work well for mobile also. Please include only photographs provided or on the old website.
Nice to have
• artistically integrated photographs. use of the logo.
Should not have
• Anything fussy.

```html
<!DOCTYPE html>
<html lang="en">
<head>
<meta charset="utf-8">
<title>Orla Thornbury – Show Jumping</title>
<link href="https://fonts.googleapis.com/css2?family=Montserrat:wght@500;600;700&family=Mulish:wght@400;600;700&display=swap" rel="stylesheet">
<style>
:root{
  --charcoal:#2b2c31;
  --charcoal-deep:#27282c;
  --panel:#4f4f52;
  --footer:#575759;
  --bar:#2f3035;
  --gold:#c7b37e;
  --white:#ffffff;
  --text:#e9e9ea;
  --rule:#55565b;
}
*{box-sizing:border-box;margin:0;padding:0}
html,body{width:1200px;height:3112px;overflow:hidden;background:var(--charcoal)}
body{font-family:"Mulish",sans-serif;color:var(--text);position:relative}
.abs{position:absolute}
a{color:inherit;text-decoration:none}
.icon-go{display:inline-block;width:13px;height:13px;vertical-align:-1px;margin-left:3px}

/* header */
.site-header{left:0;top:0;width:1200px;height:144px;background:var(--charcoal)}
.header-meta{font-size:14px;line-height:22px;color:var(--white)}
.header-meta strong{font-weight:700;font-size:14px}
.meta-icon{width:42px;height:42px}
.brand{left:429px;top:40px;width:262px;text-align:center;font-family:"Montserrat",sans-serif;font-weight:600;font-size:30px;color:var(--white);letter-spacing:1px}
.main-nav a{position:absolute;top:100px;font-size:18.5px;color:var(--white)}
.main-nav a.current{color:var(--gold);font-weight:700}

/* hero */
.hero{left:0;top:144px;width:1200px;height:581px;
  background:
   radial-gradient(ellipse 260px 300px at 560px 200px,rgba(110,80,50,.75),transparent 70%),
   linear-gradient(180deg,#4c4f58 0%,#5d5a55 35%,#3d4a66 62%,#c2a23a 80%,#6f6c68 100%)}
.hero-shade{left:0;top:144px;width:1200px;height:581px;background:rgba(20,20,24,.28)}
.hero-title{left:0;top:335px;width:1200px;text-align:center;font-family:"Montserrat",sans-serif;font-weight:700;font-size:44px;color:var(--white);letter-spacing:1px}
.hero-lede{left:250px;top:388px;width:700px;text-align:center;font-family:"Montserrat",sans-serif;font-weight:600;font-size:18px;line-height:35px;color:var(--white)}
.btn{display:flex;align-items:center;justify-content:center;height:53px;border-radius:27px;font-family:"Montserrat",sans-serif;font-weight:600;font-size:18px}
.btn-gold{background:var(--gold);color:var(--white)}
.btn-outline{border:3px solid var(--white);color:var(--white)}

/* welcome */
.welcome-title{left:0;top:790px;width:1200px;text-align:center;font-family:"Montserrat",sans-serif;font-weight:700;font-size:38px;color:var(--gold)}
.welcome-text{left:108px;top:840px;width:984px;text-align:center;font-size:15px;line-height:36px;color:var(--white)}

/* section heads */
.sec-head{display:flex;justify-content:space-between;align-items:flex-end;border-bottom:1px solid var(--rule);padding-bottom:8px}
.sec-head h3{font-family:"Montserrat",sans-serif;font-weight:700;color:var(--gold);font-size:18px}
.sec-head h2{font-family:"Montserrat",sans-serif;font-weight:700;color:var(--gold);font-size:28px;line-height:1}
.view-more{font-size:14px;color:var(--white);text-transform:uppercase;letter-spacing:.2px}

.photo{position:absolute}
.ph-jump{background:linear-gradient(180deg,#8fb3d6 0%,#cfd9e3 40%,#a57c55 70%,#cdb697 100%)}
.ph-portrait{background:linear-gradient(135deg,#4a3222 0%,#6c4a31 45%,#2c3a30 75%,#d9d9d6 100%)}
.ph-field{background:linear-gradient(160deg,#6f8c4a 0%,#5a4131 45%,#e8e8ea 80%,#6f9247 100%)}
.ph-grass{background:linear-gradient(180deg,#6b6a62 0%,#7a5a3c 45%,#4f8b34 80%,#3e7a2c 100%)}
.ph-crowd{background:linear-gradient(180deg,#4a4f67 0%,#8a6f66 45%,#b3744a 70%,#d8c4a6 100%)}
.ph-tents{background:linear-gradient(180deg,#cfd8de 0%,#5f7e45 40%,#e9ecef 65%,#c74c4c 82%,#d9c6a8 100%)}
.ph-mono{background:linear-gradient(160deg,#cfcfcf 0%,#6c6c6c 40%,#2d2d2d 80%,#5a5a5a 100%)}
.ph-mono-sm{background:linear-gradient(135deg,#d5d5d5,#5a5a5a)}
.ph-green-sm{background:linear-gradient(180deg,#6f8f55 0%,#4f7a38 55%,#c9b79a 100%)}
.ph-blue-sm{background:linear-gradient(135deg,#2d4a8a 0%,#d8c39a 50%,#1f3468 100%)}
.ph-arena{background:linear-gradient(180deg,#d9dce0 0%,#7a8f6a 30%,#6b4a33 55%,#2d3f73 80%,#d8d6d2 100%)}

/* news */
.news-lead-text{left:107px;top:2067px;width:480px;color:var(--white)}
.news-lead-text h4{font-family:"Montserrat",sans-serif;font-weight:700;font-size:18px;margin-bottom:8px}
.meta-date{font-size:13px;display:flex;align-items:center;gap:4px}
.news-lead-text p{font-size:13.5px;line-height:22px;margin-top:6px}
.news-item{position:absolute;left:605px;width:504px;height:106px;background:var(--panel)}
.news-item .thumb{position:absolute;left:5px;top:5px;width:97px;height:96px}
.news-item h4{position:absolute;left:117px;top:16px;font-family:"Montserrat",sans-serif;font-weight:700;font-size:17.5px;color:var(--white)}
.news-item .meta-date{position:absolute;left:117px;top:46px;color:var(--white)}
.news-item .more{position:absolute;left:117px;top:72px;font-size:13px;color:var(--white)}

/* about */
.about-text{left:91px;top:2300px;width:494px;font-size:15px;line-height:32.2px;text-align:justify;color:var(--white)}

/* footer */
.site-footer{left:0;top:2755px;width:1200px;height:293px;background:var(--footer)}
.foot-col h5{font-family:"Montserrat",sans-serif;font-weight:700;font-size:17.5px;color:var(--white);text-transform:uppercase;margin-bottom:20px}
.foot-col ul{list-style:none}
.foot-col li{font-size:15.5px;line-height:31.4px;color:var(--white);display:flex;align-items:center;gap:6px}
.caret{width:5px;height:9px}
.contact-row{position:absolute;left:864px;display:flex;align-items:center;gap:12px;font-size:14px;line-height:22px;color:var(--white)}
.contact-ico{width:34px;height:34px;background:var(--gold);display:flex;align-items:center;justify-content:center;flex:none}
.bottom-bar{left:0;top:3048px;width:1200px;height:64px;background:var(--bar);font-size:14px;color:var(--white)}
</style>
</head>
<body>

<svg width="0" height="0" style="position:absolute">
  <defs>
    <symbol id="go" viewBox="0 0 16 16"><circle cx="8" cy="8" r="6.6" fill="none" stroke="currentColor" stroke-width="1.8"/><path d="M4.5 8h5.5M7.8 5.4 10.4 8 7.8 10.6" fill="none" stroke="currentColor" stroke-width="1.8"/></symbol>
    <symbol id="cal" viewBox="0 0 12 12"><rect x="1" y="2" width="10" height="9" fill="none" stroke="currentColor" stroke-width="1.3"/><path d="M1 5h10M4 1v2M8 1v2M3.5 7h1M6 7h1M8.5 7h1M3.5 9h1M6 9h1" stroke="currentColor" stroke-width="1.2"/></symbol>
    <symbol id="caret" viewBox="0 0 5 9"><path d="M0 0l5 4.5L0 9z" fill="currentColor"/></symbol>
  </defs>
</svg>

<!-- header -->
<header class="site-header abs">
  <div class="abs" style="left:175px;top:30px;display:flex;gap:4px;align-items:center">
    <svg class="meta-icon" viewBox="0 0 42 42"><circle cx="21" cy="21" r="18" fill="none" stroke="#c7b37e" stroke-width="3"/><path d="M14 13c2-2 4 0 5 2s0 3-1 4c1 2 3 4 5 5 1-1 2-2 4-1s4 3 2 5c-3 3-8 1-12-3s-6-9-3-12z" fill="#c7b37e"/></svg>
    <div class="header-meta">Call us:<br><strong>+1 555 010 0199</strong></div>
  </div>
  <div class="brand abs">Orla Thornbury</div>
  <div class="abs" style="left:818px;top:30px;display:flex;gap:6px;align-items:center">
    <svg class="meta-icon" viewBox="0 0 42 42"><circle cx="17" cy="17" r="12" fill="none" stroke="#c7b37e" stroke-width="3"/><path d="M26 26l12 12" stroke="#c7b37e" stroke-width="5" stroke-linecap="round"/></svg>
    <div class="header-meta">Search:<br><strong>Enter search here</strong></div>
  </div>
  <nav class="main-nav">
    <a class="current" style="left:88px">About Us</a>
    <a style="left:219px">Horses</a>
    <a style="left:327px">Sponsors</a>
    <a style="left:709px">Facilities &amp; Services</a>
    <a style="left:928px">Gallery</a>
    <a style="left:1037px">Contact</a>
  </nav>
</header>

<!-- hero -->
<section class="hero abs" role="img" aria-label="Rider and horse clearing a fence in a packed international show arena"></section>
<div class="hero-shade abs"></div>
<h1 class="hero-title abs">ORLA THORNBURY</h1>
<p class="hero-lede abs">Lorem ipsum dolor sit amet, consectetur adipiscing elit, sed do eiusmod tempor incididunt ut labore et dolore magna aliqua.</p>
<a class="btn btn-gold abs" style="left:499px;top:472px;width:202px">Read More<svg class="icon-go"><use href="#go"/></svg></a>

<!-- welcome -->
<h2 class="welcome-title abs">WELCOME TO ORLA THORNBURY</h2>
<p class="welcome-text abs">From Castlemere in Co. Kildare, Orla is 31 years old and has been passionate about horses since she was a child. Over the years she has achieved many successes with a variety of equine partners, from Pony National Champion two years running on Harbour Lights to Senior National Champion and Nations Cup team-member on Starlight Meadow in more recent years. Having completed her studies in Liffey Valley College in 2010, her main focus now is running a small private show jumping stable from her home in Castlemere, producing younger horses right up the ranks to Grand Prix level as well as coaching students of all levels.</p>
<a class="btn btn-gold abs" style="left:388px;top:1041px;width:202px">Read More<svg class="icon-go"><use href="#go"/></svg></a>
<a class="btn btn-outline abs" style="left:609px;top:1041px;width:202px">Contact Us<svg class="icon-go"><use href="#go"/></svg></a>

<!-- horse categories -->
<div class="sec-head abs" style="left:89px;top:1168px;width:322px"><h3>Current Horses</h3><a class="view-more">View more<svg class="icon-go"><use href="#go"/></svg></a></div>
<div class="sec-head abs" style="left:439px;top:1168px;width:322px"><h3>Reference Horses</h3><a class="view-more">View more<svg class="icon-go"><use href="#go"/></svg></a></div>
<div class="sec-head abs" style="left:788px;top:1168px;width:321px"><h3>High Quality Horses</h3><a class="view-more">View more<svg class="icon-go"><use href="#go"/></svg></a></div>
<div class="photo ph-jump" style="left:89px;top:1215px;width:322px;height:199px" role="img" aria-label="Horse and rider jumping a coloured fence on a sand arena"></div>
<div class="photo ph-portrait" style="left:439px;top:1215px;width:322px;height:199px" role="img" aria-label="Close view of a bay horse beside its rider in competition jacket"></div>
<div class="photo ph-field" style="left:788px;top:1215px;width:321px;height:199px" role="img" aria-label="Bay horse standing with its rider on a grass showground"></div>

<!-- photo albums -->
<div class="sec-head abs" style="left:89px;top:1484px;width:1020px"><h2>Recent Photos Albums</h2><a class="view-more">View more<svg class="icon-go"><use href="#go"/></svg></a></div>
<div class="photo ph-grass" style="left:89px;top:1536px;width:322px;height:199px" role="img" aria-label="Horse and rider taking off over a fence on grass"></div>
<div class="photo ph-crowd" style="left:439px;top:1536px;width:322px;height:199px" role="img" aria-label="Show jumping round in front of a full grandstand"></div>
<div class="photo ph-tents" style="left:788px;top:1536px;width:321px;height:199px" role="img" aria-label="Rider jumping a red fence with white marquees behind"></div>

<!-- news -->
<div class="sec-head abs" style="left:89px;top:1806px;width:1020px"><h2>News &amp; Events</h2><a class="view-more">View more<svg class="icon-go"><use href="#go"/></svg></a></div>
<div class="photo ph-mono" style="left:91px;top:1857px;width:504px;height:330px" role="img" aria-label="Black and white image of a rider leaning over a horse's neck"></div>
<div class="news-lead-text abs">
  <h4>Sed ut perspiciatis unde omnis iste natus</h4>
  <div class="meta-date"><svg width="12" height="12"><use href="#cal"/></svg>11 November 2019</div>
  <p>Sed ut perspiciatis unde omnis iste natus error sit voluptatem accusantium doloremque laudantium, dicta sunt explicabo.</p>
</div>

<article class="news-item" style="top:1857px">
  <div class="thumb ph-mono-sm" role="img" aria-label="Black and white image of a horse at a show"></div>
  <h4>Sed ut perspiciatis unde omnis iste natus</h4>
  <div class="meta-date"><svg width="12" height="12"><use href="#cal"/></svg>11 November 2019</div>
  <a class="more">Read More<svg class="icon-go"><use href="#go"/></svg></a>
</article>
<article class="news-item" style="top:1970px">
  <div class="thumb ph-green-sm" role="img" aria-label="Horse and rider on a green showground"></div>
  <h4>Sed ut perspiciatis unde omnis iste natus</h4>
  <div class="meta-date"><svg width="12" height="12"><use href="#cal"/></svg>11 November 2019</div>
  <a class="more">Read More<svg class="icon-go"><use href="#go"/></svg></a>
</article>
<article class="news-item" style="top:2082px">
  <div class="thumb ph-blue-sm" role="img" aria-label="Rider in team cap at a show"></div>
  <h4>Sed ut perspiciatis unde omnis iste natus</h4>
  <div class="meta-date"><svg width="12" height="12"><use href="#cal"/></svg>11 November 2019</div>
  <a class="more">Read More<svg class="icon-go"><use href="#go"/></svg></a>
</article>

<!-- about -->
<div class="sec-head abs" style="left:89px;top:2258px;width:1020px"><h2>About Us</h2><a class="view-more">View more<svg class="icon-go"><use href="#go"/></svg></a></div>
<p class="about-text abs">Orla is an accomplished rider, sport horse producer and equestrian-coach. Following the purchase of the seven-year-old gelding “Starlight Meadow” from Holland, at the age of just 16 Orla and he formed an exceptional partnershipand successfully progressed through the ranks to the very top level of show jumping on a global scale.<br>Over the next few years the partnership would make four European Championship team appearances for Ireland, win a Senior National Championship title (still being the youngest female every to do so), achieve global success at CSI5* level and achieve theultimate Irish rider’s dream of selection for the Irish Team competing in the Nations Cup Trophy at the Leinster Horse Show, where Orla helped Ireland to finish in run-ner-upposition.</p>
<div class="photo ph-arena" style="left:605px;top:2311px;width:504px;height:363px" role="img" aria-label="Horse and rider clearing a blue fence with a scoreboard behind"></div>

<!-- footer -->
<footer class="site-footer abs">
  <div class="foot-col abs" style="left:91px;top:43px">
    <h5>Customer Service</h5>
    <ul>
      <li><svg class="caret"><use href="#caret"/></svg>Home</li>
      <li><svg class="caret"><use href="#caret"/></svg>About</li>
      <li><svg class="caret"><use href="#caret"/></svg>Horses</li>
      <li><svg class="caret"><use href="#caret"/></svg>Sponsors</li>
      <li><svg class="caret"><use href="#caret"/></svg>Gallery</li>
    </ul>
  </div>
  <div class="foot-col abs" style="left:366px;top:43px">
    <h5>Quick Links</h5>
    <ul>
      <li><svg class="caret"><use href="#caret"/></svg>News</li>
      <li><svg class="caret"><use href="#caret"/></svg>Facilities &amp; Services</li>
      <li><svg class="caret"><use href="#caret"/></svg>FAQ &amp; Help</li>
    </ul>
  </div>
  <div class="foot-col abs" style="left:624px;top:43px">
    <h5>Other Links</h5>
    <ul>
      <li><svg class="caret"><use href="#caret"/></svg>Contact us</li>
      <li><svg class="caret"><use href="#caret"/></svg>Blog</li>
      <li><svg class="caret"><use href="#caret"/></svg>Privacy Policy</li>
    </ul>
  </div>
  <div class="foot-col abs" style="left:864px;top:43px"><h5>Contact Us</h5></div>
  <div class="contact-row" style="top:92px">
    <span class="contact-ico"><svg width="14" height="18" viewBox="0 0 14 18"><path d="M7 0a7 7 0 0 0-7 7c0 5 7 11 7 11s7-6 7-11a7 7 0 0 0-7-7z" fill="#fff"/><circle cx="7" cy="7" r="2.5" fill="#c7b37e"/></svg></span>
    <span>Ballyrowan, Castlemere, Co.<br>Kildare, Ireland</span>
  </div>
  <div class="contact-row" style="top:152px">
    <span class="contact-ico"><svg width="16" height="12" viewBox="0 0 16 12"><rect width="16" height="12" fill="#fff"/><path d="M0 0l8 7 8-7" fill="none" stroke="#c7b37e" stroke-width="1.5"/></svg></span>
    <span>Email: orla@orlathornbury.com</span>
  </div>
  <div class="contact-row" style="top:207px">
    <span class="contact-ico"><svg width="16" height="16" viewBox="0 0 16 16"><path d="M3 1c2-1 3 1 4 3s0 3-1 3.5c1 2 2 3 3.5 3.5.5-1 1.5-2 3.5-1s3 2 1.5 4c-2 2-6 1-9.5-2.5S1 3 3 1z" fill="#fff"/></svg></span>
    <span>Phone: +353 87 555 0142</span>
  </div>
</footer>

<div class="bottom-bar abs">
  <span class="abs" style="left:91px;top:22px">Copyright © 2019. All Right Reserved.</span>
  <span class="abs" style="left:793px;top:22px;word-spacing:2px">Site Map &nbsp;|&nbsp; Returns &nbsp;|&nbsp; Terms of use &nbsp;|&nbsp; Affiliate</span>
</div>

</body>
</html>
```